Upstart Retirement Planning Firm needs help with business card design

Harborview Nest Advisors, LLC is looking for help with business card design. We give advice on investments, insurance, and other financial matters related to retirement. There are some required disclosures that we will provide but mostly we are looking for a professional, classy business card that reflects the theme we have chosen. We have a logo that is attached but we would like to add a phrase; "Turning Your Earned Income Into Retirement Income"

Doubled sided only so that we can add the required disclosures (needed for our industry) on the back of the card. We will provide the exact words for this in 1-2 days.

Target Market(s)

Retirees and Pre-retirees. Professionals 50+ years old

Industry/Entity Type

Financial Planning

Contact Information for Business Card

We currently have two people who will need separate cards so we'd like to have a template so that we can add names for new cards in the future.

For the first run, please show the following information.

Gregor Pelham, MBA, ChFC®, CLU®
Financial Advisor, Registered Representative
gpelham@harborviewnest.example
Phone: (555) 318-2946
Toll Free Fax: (800) 555-0193

Address is
2187 Meadowlark Ridge Rd.
Suite K418
Virginia Beach, VA 23999

Colors
3277b5

Requirements
Must have
• Logo, contact info, small phase to describe business (in description), required legal disclosures on back of the card as follows (in small font)
• Gregor Pelham is a registered representative of and offers securities through Brightmoor Capital Brokerage Corporation, Member FNQX. Brightmoor Capital Brokerage Corporation is a member of the Brightmoor Capital Alliance which is the marketing name for Brightmoor Holding Corporation and its affiliates.
Nice to have
• Rounded edges, raised letters
Should not have
• any colors that aren't in the logo (other than black for font)

```html
<!DOCTYPE html>
<html lang="en">
<head>
<meta charset="utf-8">
<title>Harborview Nest Advisors – Business Cards</title>
<link href="https://fonts.googleapis.com/css2?family=Arimo:wght@400;700&display=swap" rel="stylesheet">
<style>
  :root {
    --backdrop: #3a322e;
    --card: #17181a;
    --card-edge: #232427;
    --brand-blue: #3277b5;
    --text-light: #e9e9ea;
    --text-muted: #a9aaae;
    --rule: #d8d8da;
  }
  * { box-sizing: border-box; margin: 0; padding: 0; }
  html, body {
    width: 1200px; height: 787px; overflow: hidden;
    background: var(--backdrop);
    font-family: "Arimo", Arial, sans-serif;
  }
  .stage { position: relative; width: 1200px; height: 787px; }
  .card {
    position: absolute; top: 245px;
    width: 520px; height: 298px;
    background: var(--card);
    border: 1px solid var(--card-edge);
    border-radius: 14px;
    box-shadow: 0 12px 28px rgba(0,0,0,0.45);
    color: var(--text-light);
    overflow: hidden;
  }
  .card--brand { left: 60px; }
  .card--contact { left: 620px; }

  /* Brand side */
  .brand-name {
    position: absolute; left: 0; right: 0; top: 70px;
    text-align: center;
    font-size: 26px; font-weight: 400; letter-spacing: 0.5px;
    color: var(--brand-blue);
    white-space: nowrap;
  }
  .brand-mark {
    display: inline-block; width: 12px; height: 12px;
    border-radius: 50%; background: var(--brand-blue);
    margin-right: 10px; vertical-align: middle;
  }
  .tagline {
    position: absolute; left: 30px; right: 30px; top: 138px;
    text-align: center;
    font-size: 14px; color: var(--brand-blue);
  }
  .disclosure {
    position: absolute; left: 30px; right: 30px; top: 206px;
    text-align: center;
    font-size: 9px; line-height: 13px; color: var(--text-muted);
  }

  /* Contact side */
  .contact-logo {
    position: absolute; right: 28px; top: 28px;
    text-align: right; white-space: nowrap;
    font-size: 16px; color: var(--brand-blue);
  }
  .person { position: absolute; left: 28px; top: 68px; }
  .person-name { font-size: 19px; color: var(--brand-blue); white-space: nowrap; }
  .person-name .credentials { font-size: 11px; margin-left: 4px; }
  .person-title { font-size: 12.5px; margin-top: 6px; color: var(--text-light); }
  .contact-list {
    position: absolute; left: 28px; top: 128px;
    list-style: none; font-size: 14px; line-height: 22px;
  }
  .contact-list li { display: flex; align-items: center; white-space: nowrap; }
  .contact-list svg { width: 13px; height: 13px; margin-right: 8px; fill: var(--brand-blue); flex: none; }
  .divider {
    position: absolute; left: 28px; right: 28px; top: 204px;
    height: 1px; background: var(--rule);
  }
  .address {
    position: absolute; right: 28px; top: 214px;
    text-align: right; font-size: 14px; line-height: 21px; font-style: normal;
  }
</style>
</head>
<body>
<main class="stage">
  <section class="card card--brand" aria-label="Card front">
    <div class="brand-name"><span class="brand-mark"></span>Harborview Nest Advisors, LLC</div>
    <p class="tagline">Turning Your Earned Income Into Retirement Income</p>
    <p class="disclosure">Gregor Pelham is a registered representative of and offers securities through Brightmoor Capital Brokerage Corporation, Member FNQX. Brightmoor Capital Brokerage Corporation is a member of the Brightmoor Capital Alliance which is the marketing name for Brightmoor Holding Corporation and its affiliates.</p>
  </section>

  <section class="card card--contact" aria-label="Card back">
    <div class="contact-logo">Harborview Nest Advisors, LLC</div>
    <div class="person">
      <p class="person-name">Gregor Pelham,<span class="credentials">MBA, ChFC®, CLU®</span></p>
      <p class="person-title">Financial Advisor, Registered Representative</p>
    </div>
    <ul class="contact-list">
      <li><svg viewBox="0 0 16 16" aria-hidden="true"><path d="M3.6 1.2l2.3 2.3c.4.4.4 1 0 1.4L4.7 6.1c.9 2 2.6 3.7 4.6 4.6l1.2-1.2c.4-.4 1-.4 1.4 0l2.3 2.3c.4.4.4 1 0 1.4l-1.3 1.3C11 16.4 0 5.4 2.3 1.2z"/></svg>(555) 318-2946</li>
      <li><svg viewBox="0 0 16 16" aria-hidden="true"><path d="M3.6 1.2l2.3 2.3c.4.4.4 1 0 1.4L4.7 6.1c.9 2 2.6 3.7 4.6 4.6l1.2-1.2c.4-.4 1-.4 1.4 0l2.3 2.3c.4.4.4 1 0 1.4l-1.3 1.3C11 16.4 0 5.4 2.3 1.2z"/></svg>(800) 555-0193 (Toll Free Fax)</li>
      <li><svg viewBox="0 0 16 16" aria-hidden="true"><path d="M1 3h14v1.2L8 9 1 4.2z M1 5.6l7 4.8 7-4.8V13H1z"/></svg>gpelham@harborviewnest.example</li>
    </ul>
    <div class="divider"></div>
    <address class="address">
      2187 Meadowlark Ridge Rd.<br>
      Suite K418<br>
      Virginia Beach, VA 23999
    </address>
  </section>
</main>
</body>
</html>
```